We need a modern WIX website for Brightform Beam Services Australia (Laser/Industrial/Engineering)

We need a website for Wix (coded) for our laser restoration and industrial cleaning business.

It will need to be 4-6 pages.
Pages may include:
Home
About
Why Laser
Capabilities
There needs to be a contact / quote form

We do not want boring institutional design, so please do try to be a little creative (but not artsy, more engineering / laser etc). We hesitate with boxy wordpress looking templates, so please bring in strip backgrounds and sliders etc;

Our brand colours are blue and red, but a sharp modern site relative to the industry and work is important.

We envision the home page to take visitors on a informed journey of who, what, why, how, explaining the capability of laser science across contaminants, industries and surfaces.

We envision the home page to be strips:
- landing
- intro

-Why choose laser / What is laser cleaning
Minimum downtime, no surface damage, no environmental impact, no mess, no waste, complete restoration (we have an explainer video)

- Contaminants
Bacteria, Rust, Corrosion, Oxides, Grease, Oil, Paint, Stains, Mold, Soot / Carbon, Graffiti, Coatings, Dirt, Residue

- Surfaces
Metals, Engines/Parts/Components, Tools, Machinery, Bricks/Blockwork, Concrete, Paint, Stone, Wood, Aluminium

- Industries
Medical/Sterile, Hospitality, Bio Hazardous, Construction, Infrastructure, Property, Industrial, Engineer, Automotive, Marine, Heritage, Non Destructive Testing,

----
Here is some info on the company below:

"Background Information - Brightform Beam Services Australia (BBSA) is a leading provider of advanced laser restoration services for the residential, commercial, medical, hazardous and industrial sectors, offering waste free, chemical free and damage free complete restoration of metals, concrete, wood, stone and heritage, hygiene and hazard surfaces, with complete removal of coatings, bacteria, paint, rust, graffiti, mold and fire ash (soot), and preparation and treating for welding and bonding.
Servicing Melbourne and Victoria, with additional services available Australia wide, BBSA offers a 24/7 call-out service to your site.
With no downtime to your operations, we offer a timely resolution to your cleaning and maintenance needs."

We have attached some inspiration of websites we like the flow/feel of, but feel free to put your best designs forward.

You are welcome to use dummy headers and text at this stage, as design and feel is most important, and we can add text later.

```html
<!DOCTYPE html>
<html lang="en">
<head>
<meta charset="utf-8">
<title>Brightform Beam Services Australia</title>
<link href="https://fonts.googleapis.com/css2?family=Oswald:wght@300;400;500&family=Michroma&family=Lato:wght@400;700&display=swap" rel="stylesheet">
<style>
:root{
  --red:#e31e24;
  --blue:#1670c4;
  --ink:#111111;
  --night:#0e0e0e;
  --slate:#2b2b2b;
  --white:#ffffff;
  --muted:#cfcfcf;
  --wide:"Michroma",sans-serif;
  --cond:"Oswald",sans-serif;
  --body:"Lato",sans-serif;
}
*{margin:0;padding:0;box-sizing:border-box}
html,body{width:1200px;height:4556px;overflow:hidden}
body{position:relative;background:var(--white);font-family:var(--body);color:var(--ink)}
.abs{position:absolute}

/* top bar */
.topbar{left:0;top:0;width:1200px;height:55px;background:var(--red);color:var(--white);font-family:var(--wide);font-size:13px;letter-spacing:.5px;text-transform:uppercase}
.topbar span{position:absolute;top:19px}
.topbar svg{position:absolute;top:18px}

/* nav */
.nav{left:0;top:55px;width:1200px;height:86px;background:var(--white)}
.brand{display:flex;align-items:center;gap:10px;font-family:var(--cond);font-weight:500;color:var(--red);font-size:46px;letter-spacing:3px;line-height:1}
.brand i{display:block;width:22px;height:22px;background:var(--blue)}
.nav a{position:absolute;top:36px;font-family:var(--wide);font-size:13px;color:var(--ink);text-decoration:none;text-transform:uppercase}
.nav a.active{color:var(--red)}
.nav .cta{left:951px;top:23px;width:145px;height:42px;background:var(--blue);color:var(--white);display:flex;align-items:center;justify-content:center;box-shadow:0 3px 6px rgba(0,0,0,.3);font-size:12px}

/* hero */
.hero-photo{left:0;top:141px;width:1200px;height:560px;background:radial-gradient(circle at 760px 330px,#e8a24a 0,#7a4a2a 9%,#1c2a4a 30%,#0c1530 65%,#060a16 100%)}
.hero-shape{left:0;top:141px}
.kicker{font-family:var(--wide);font-size:12px;letter-spacing:1px;text-transform:uppercase}
.hero-kicker{left:111px;top:228px;color:var(--white)}
.hero-title{left:111px;top:254px;width:580px;color:var(--white);font-family:var(--cond);font-weight:400;font-size:49px;line-height:60px}
.btn{display:flex;align-items:center;gap:14px;background:var(--white);font-family:var(--wide);font-size:14px;color:var(--ink);padding-left:14px;text-transform:uppercase}
.btn i{width:36px;height:36px;background:var(--red);display:block}
.hero-btn{left:111px;top:454px;width:228px;height:55px}
.dots{left:563px;top:644px;display:flex;gap:12px}
.dots b{width:11px;height:11px;border-radius:50%;background:#555;display:block}
.dots b.on{background:var(--white)}

/* about */
.dark-band{left:0;top:760px;width:1200px;height:972px;background:var(--night)}
.about-ghost{left:-90px;top:990px;width:420px;transform:rotate(-90deg);font-family:var(--cond);font-weight:300;font-size:120px;letter-spacing:8px;color:transparent;-webkit-text-stroke:2px #3a3a3a;text-align:center}
.frame-red{left:180px;top:802px;width:283px;height:396px;border:7px solid var(--red)}
.about-photo{left:208px;top:843px;width:357px;height:496px;background:linear-gradient(160deg,#3a8c8f 0%,#1d4b5a 40%,#c0b489 70%,#f1e6c8 85%,#2a2a2a 100%)}
.bracket{left:565px;top:945px;width:23px;height:393px;border:5px solid var(--white);border-left:none}
.red-block{left:208px;top:1339px;width:145px;height:48px;background:var(--red)}
.about-kicker{left:659px;top:831px;color:var(--red)}
.about-title{left:659px;top:855px;width:430px;color:var(--white);font-family:var(--cond);font-weight:400;font-size:30px;line-height:42px;text-transform:uppercase}
.about-copy{left:659px;top:948px;width:430px;color:#e8e8e8;font-size:14.5px;line-height:25.6px;text-align:justify}
.about-copy p+p{margin-top:25px}
.about-btn{left:659px;top:1330px;width:214px;height:55px}

/* video */
.video{left:111px;top:1451px;width:977px;height:493px;border:3px solid var(--red);border-radius:16px;background:radial-gradient(circle at 490px 300px,#f0b060 0,#9a5a2a 12%,#3a3636 40%,#1a1a1a 100%);overflow:hidden}
.video-brand{position:absolute;right:34px;top:26px;font-family:var(--cond);font-weight:500;color:var(--white);font-size:28px;letter-spacing:2px}
.play{left:573px;top:1684px;width:60px;height:60px;border-radius:50%;background:var(--red)}
.play::after{content:"";position:absolute;left:24px;top:19px;border-left:17px solid var(--white);border-top:11px solid transparent;border-bottom:11px solid transparent}

/* section heads */
.ghost{left:0;width:1200px;text-align:center;font-family:var(--cond);font-weight:300;font-size:138px;letter-spacing:10px;color:transparent;line-height:1;text-transform:uppercase}
.ghost.light{-webkit-text-stroke:1.5px #e1e1e1}
.ghost.dim{-webkit-text-stroke:1.5px #4a4a4a}
.ghost.deep{-webkit-text-stroke:1.5px #222}
.sec-kicker{left:0;width:1200px;text-align:center;font-family:var(--wide);font-size:12px;letter-spacing:2px;text-transform:uppercase}
.sec-title{left:0;width:1200px;text-align:center;font-family:var(--cond);font-weight:400;font-size:30px;text-transform:uppercase}

.arrow{width:26px;height:26px;border-radius:50%;background:var(--ink)}
.arrow.pale{background:var(--white)}
.arrow::after{content:"";position:absolute;left:9px;top:9px;width:7px;height:7px;border-left:2.5px solid var(--white);border-bottom:2.5px solid var(--white);transform:rotate(45deg)}
.arrow.next::after{left:7px;transform:rotate(-135deg)}
.arrow.pale::after{border-color:var(--ink)}

/* why cards */
.card{width:296px;height:325px;background:var(--white);border-radius:10px;box-shadow:0 4px 12px rgba(0,0,0,.18);overflow:hidden}
.card .shot{height:274px}
.card .pill{position:absolute;left:18px;right:18px;bottom:2px;height:78px;background:var(--white);border-radius:14px 14px 0 0;display:flex;align-items:center;justify-content:center;text-align:center;font-family:var(--wide);font-size:12.5px;line-height:22px;text-transform:uppercase;white-space:nowrap}

/* grey strip */
.grey-band{left:0;top:2545px;width:1200px;height:503px;background:linear-gradient(135deg,#2f2f2f,#262626)}
.tri{width:190px;height:170px}
.tri-label{width:200px;text-align:center;font-family:var(--wide);font-size:17px;letter-spacing:1px;text-transform:uppercase}

/* industries */
.ind-band{left:0;top:3503px;width:1200px;height:579px;background:#151515}
.ind-card{width:301px;height:321px;background:var(--white);border-radius:8px;overflow:hidden}
.ind-card.hot{border:3px solid var(--red)}
.ind-card .shot{height:276px}
.ind-card .pill{position:absolute;left:22px;right:22px;bottom:10px;height:58px;background:var(--white);border-radius:14px 14px 0 0;display:flex;align-items:center;justify-content:center;font-family:var(--wide);font-size:13px;text-transform:uppercase}

/* footer */
.footer{left:0;top:4082px;width:1200px;height:474px;background:#0a0a0a;color:var(--white)}
.f-title{position:absolute;top:101px;font-family:var(--wide);font-size:13px;text-transform:uppercase}
.f-text{position:absolute;font-size:13px;line-height:22px;color:#e5e5e5}
.f-input{position:absolute;left:385px;top:186px;width:232px;height:45px;background:var(--blue);font-size:13px;font-weight:700;padding:14px 20px}
.f-sub{position:absolute;left:385px;top:247px;width:165px;height:55px;background:var(--red);display:flex;align-items:center;gap:12px;padding-left:8px;font-weight:700;font-size:17px}
.f-sub i{width:36px;height:36px;background:var(--white);display:block}
.f-ico{position:absolute;left:693px;width:32px;height:32px;background:var(--white);border-radius:4px}
.f-link{position:absolute;left:928px;font-size:14px;color:#e5e5e5}
.f-link::before{content:"→";margin-right:10px;color:var(--white)}
.f-rule{position:absolute;left:111px;top:378px;width:977px;height:1px;background:#555}
.f-copy{position:absolute;left:0;top:416px;width:1200px;text-align:center;font-size:12px;color:#e5e5e5}
</style>
</head>
<body>

<div class="abs topbar">
  <svg width="18" height="18" viewBox="0 0 24 24" style="left:110px"><path d="M6 3l3 4-2 2c1 3 4 6 7 7l2-2 4 3-2 4C10 21 3 14 3 5z" fill="none" stroke="#fff" stroke-width="2"/></svg>
  <span style="left:168px">Call:+61 3 9000 4417</span>
  <svg width="18" height="18" viewBox="0 0 24 24" style="left:404px"><rect x="2" y="5" width="20" height="14" fill="#fff"/><path d="M2 5l10 8 10-8" fill="none" stroke="#e31e24" stroke-width="2"/></svg>
  <span style="left:463px">Mail:info@bbsa.com</span>
</div>

<div class="abs nav">
  <div class="abs brand" style="left:103px;top:20px"><i></i>BBSA</div>
  <a class="active" style="left:433px">Home</a>
  <a style="left:527px">About</a>
  <a style="left:633px">Why Laser</a>
  <a style="left:783px">Capabilities</a>
  <a class="cta">Contact Us</a>
</div>

<div class="abs hero-photo" role="img" aria-label="Industrial laser head cutting metal with a shower of sparks"></div>
<svg class="abs hero-shape" width="1200" height="620" viewBox="0 0 1200 620">
  <polygon points="0,418 600,620 1200,418 1200,620 0,620" fill="#0e0e0e"/>
  <polygon points="0,415 600,590 1200,415 1200,425 600,622 0,425" fill="#e31e24"/>
</svg>
<div class="abs kicker hero-kicker">Brightform Beam Services Australia</div>
<h1 class="abs hero-title">We are a laser restoration and<br>industrial cleaning<br>business</h1>
<div class="abs btn hero-btn"><i></i>Get Started</div>
<div class="abs dots"><b></b><b class="on"></b></div>

<div class="abs dark-band"></div>
<div class="abs about-ghost">ABOUT</div>
<div class="abs frame-red"></div>
<div class="abs about-photo" role="img" aria-label="Laser cutter nozzle working on a metal plate"></div>
<div class="abs bracket"></div>
<div class="abs red-block"></div>
<div class="abs kicker about-kicker">About Us</div>
<h2 class="abs about-title">Welcome to Brightform Beam Services Australia</h2>
<div class="abs about-copy">
  <p>Brightform Beam Services Australia (BBSA) is a leading provider of advanced laser restoration services for the residential, commercial, medical, hazardous and industrial sectors, offering waste free, chemical free and damage free complete restoration of metals, concrete, wood, stone and heritage, hygiene and hazard surfaces, with complete removal of coatings, bacteria, paint, rust, graffiti, mold and fire ash (soot), and preparation and treating for welding and bonding.<br>Servicing Melbourne and Victoria, with additional services available Australia wide, BBSA offers a 24/7 call-out service to your site.</p>
  <p>With no downtime to your operations, we offer a timely resolution to your cleaning and maintenance needs.</p>
</div>
<div class="abs btn about-btn"><i></i>Read More</div>

<div class="abs video" role="img" aria-label="Explainer video still of a laser head throwing sparks">
  <div class="video-brand">BBSA</div>
</div>
<div class="abs play"></div>

<div class="abs ghost light" style="top:1990px">Choose Laser</div>
<div class="abs sec-kicker" style="top:2030px;color:var(--red)">Laser</div>
<h2 class="abs sec-title" style="top:2050px">Why Choose Laser</h2>
<div class="abs arrow" style="left:36px;top:2302px"></div>
<div class="abs arrow next" style="left:1125px;top:2302px"></div>
<div class="abs card" style="left:111px;top:2152px">
  <div class="shot" role="img" aria-label="Dry cracked earth surface" style="background:linear-gradient(160deg,#9b7c5c,#6e5238)"></div>
  <div class="pill">No<br>Surface Damage</div>
</div>
<div class="abs card" style="left:452px;top:2152px">
  <div class="shot" role="img" aria-label="Lone tree split between barren and green landscape" style="background:linear-gradient(90deg,#d9a45a 0%,#a8864e 48%,#6aa0c8 52%,#5c9a3a 100%)"></div>
  <div class="pill">No<br>Environmental Impact</div>
</div>
<div class="abs card" style="left:792px;top:2152px">
  <div class="shot" role="img" aria-label="Hand sanding a wooden board" style="background:linear-gradient(150deg,#e6cfa6,#b89068)"></div>
  <div class="pill">Complete<br>Restoration</div>
</div>

<div class="abs grey-band"></div>
<div class="abs ghost dim" style="top:2605px">Contaminants</div>
<div class="abs sec-kicker" style="top:2644px;color:var(--white)">Laser</div>
<h2 class="abs sec-title" style="top:2664px;color:var(--white)">Contaminants We Treat</h2>
<div class="abs arrow pale" style="left:38px;top:2858px"></div>
<div class="abs arrow pale next" style="left:1127px;top:2858px"></div>

<svg class="abs tri" style="left:112px;top:2765px" viewBox="0 0 190 170"><polygon points="22,156 95,14 168,156" fill="#e31e24" stroke="#e31e24" stroke-width="26" stroke-linejoin="round"/><g fill="none" stroke="#fff" stroke-width="4"><ellipse cx="85" cy="110" rx="26" ry="14" transform="rotate(-35 85 110)"/><circle cx="80" cy="112" r="3"/><circle cx="92" cy="104" r="3"/><circle cx="122" cy="90" r="7"/><circle cx="124" cy="124" r="9"/></g></svg>
<div class="abs tri-label" style="left:107px;top:2950px;color:var(--white)">Bacteria</div>

<svg class="abs tri" style="left:308px;top:2765px" viewBox="0 0 190 170"><polygon points="22,14 168,14 95,156" fill="#1670c4" stroke="#1670c4" stroke-width="26" stroke-linejoin="round"/><g fill="none" stroke="#fff" stroke-width="5"><polygon points="95,28 124,45 124,78 95,95 66,78 66,45"/><circle cx="95" cy="61" r="14"/></g></svg>
<div class="abs tri-label" style="left:303px;top:2950px;color:var(--white)">Rust</div>

<svg class="abs tri" style="left:506px;top:2765px" viewBox="0 0 190 170"><polygon points="22,156 95,14 168,156" fill="#e31e24" stroke="#e31e24" stroke-width="26" stroke-linejoin="round"/><g fill="none" stroke="#fff" stroke-width="4"><ellipse cx="95" cy="108" rx="36" ry="13"/><ellipse cx="95" cy="108" rx="36" ry="13" transform="rotate(60 95 108)"/><ellipse cx="95" cy="108" rx="36" ry="13" transform="rotate(-60 95 108)"/><circle cx="95" cy="108" r="5" fill="#fff"/></g></svg>
<div class="abs tri-label" style="left:501px;top:2950px;color:var(--white)">Oxides</div>

<svg class="abs tri" style="left:704px;top:2765px" viewBox="0 0 190 170"><polygon points="22,14 168,14 95,156" fill="#1670c4" stroke="#1670c4" stroke-width="26" stroke-linejoin="round"/><g fill="none" stroke="#fff" stroke-width="4"><circle cx="95" cy="58" r="16"/><circle cx="70" cy="38" r="6"/><circle cx="124" cy="42" r="7"/><circle cx="120" cy="80" r="6"/><circle cx="72" cy="78" r="5"/></g></svg>
<div class="abs tri-label" style="left:699px;top:2950px;color:var(--white)">Stains</div>

<svg class="abs tri" style="left:900px;top:2765px" viewBox="0 0 190 170"><polygon points="22,156 95,14 168,156" fill="#e31e24" stroke="#e31e24" stroke-width="26" stroke-linejoin="round"/><g fill="none" stroke="#fff" stroke-width="4"><rect x="80" y="92" width="30" height="46" rx="4"/><rect x="86" y="78" width="18" height="14"/><path d="M86 82h-14v-8"/><path d="M95 108c-6 8-6 14 0 14s6-6 0-14z"/></g></svg>
<div class="abs tri-label" style="left:895px;top:2950px;color:var(--white)">Grease</div>

<div class="abs ghost light" style="top:3085px">Surfaces</div>
<div class="abs sec-kicker" style="top:3128px;color:var(--red)">BBSA</div>
<h2 class="abs sec-title" style="top:3148px">Our Surfaces</h2>
<div class="abs arrow" style="left:38px;top:3337px"></div>
<div class="abs arrow next" style="left:1127px;top:3337px"></div>

<svg class="abs tri" style="left:108px;top:3249px" viewBox="0 0 190 170"><polygon points="22,156 95,14 168,156" fill="#e31e24" stroke="#e31e24" stroke-width="26" stroke-linejoin="round"/><g fill="none" stroke="#fff" stroke-width="4"><path d="M66 130l40-40h22l-40 40z"/><path d="M74 118l40-40h22l-40 40z"/><path d="M66 130v-12l8 0"/></g></svg>
<div class="abs tri-label" style="left:103px;top:3434px">Metals</div>

<svg class="abs tri" style="left:308px;top:3249px" viewBox="0 0 190 170"><polygon points="22,14 168,14 95,156" fill="#1670c4" stroke="#1670c4" stroke-width="26" stroke-linejoin="round"/><g fill="none" stroke="#fff" stroke-width="6" stroke-linecap="round"><path d="M70 34l50 52"/><path d="M120 34l-50 52"/><circle cx="66" cy="30" r="8"/><circle cx="124" cy="90" r="8"/></g></svg>
<div class="abs tri-label" style="left:303px;top:3434px">Tools</div>

<svg class="abs tri" style="left:504px;top:3249px" viewBox="0 0 190 170"><polygon points="22,156 95,14 168,156" fill="#e31e24" stroke="#e31e24" stroke-width="26" stroke-linejoin="round"/><g fill="none" stroke="#fff" stroke-width="4"><rect x="62" y="84" width="56" height="22"/><rect x="84" y="106" width="20" height="16"/><circle cx="110" cy="128" r="10"/><path d="M94 122v16"/></g></svg>
<div class="abs tri-label" style="left:499px;top:3434px">Machinery</div>

<svg class="abs tri" style="left:702px;top:3249px" viewBox="0 0 190 170"><polygon points="22,14 168,14 95,156" fill="#1670c4" stroke="#1670c4" stroke-width="26" stroke-linejoin="round"/><g fill="none" stroke="#fff" stroke-width="5"><rect x="66" y="30" width="50" height="18" rx="3"/><path d="M116 40h10v18h-31v14"/><rect x="89" y="72" width="12" height="26" rx="3"/></g></svg>
<div class="abs tri-label" style="left:697px;top:3434px">Paint</div>

<svg class="abs tri" style="left:900px;top:3249px" viewBox="0 0 190 170"><polygon points="22,156 95,14 168,156" fill="#e31e24" stroke="#e31e24" stroke-width="26" stroke-linejoin="round"/><g fill="none" stroke="#fff" stroke-width="4"><path d="M68 80h54l-54 12h54l-54 12h54l-54 12h54l-54 12h54"/></g></svg>
<div class="abs tri-label" style="left:895px;top:3434px">Aluminium</div>

<div class="abs ind-band"></div>
<div class="abs ghost deep" style="top:3538px">Industries</div>
<div class="abs sec-kicker" style="top:3575px;color:var(--red)">BBSA</div>
<h2 class="abs sec-title" style="top:3595px;color:var(--white)">Industries We Serve</h2>
<div class="abs arrow pale" style="left:36px;top:3839px"></div>
<div class="abs arrow pale next" style="left:1125px;top:3839px"></div>
<div class="abs ind-card" style="left:111px;top:3690px">
  <div class="shot" role="img" aria-label="Laboratory worker handling sterile equipment" style="background:linear-gradient(150deg,#9db7c8,#4d6b82)"></div>
  <div class="pill">Medical/Sterile</div>
</div>
<div class="abs ind-card hot" style="left:449px;top:3690px">
  <div class="shot" role="img" aria-label="Clean factory production line" style="background:linear-gradient(160deg,#d8dde2,#7f8b94)"></div>
  <div class="pill">Hospitality</div>
</div>
<div class="abs ind-card" style="left:788px;top:3690px">
  <div class="shot" role="img" aria-label="Steam cleaner releasing vapour on dark floor" style="background:linear-gradient(160deg,#3a3a3a,#9a9a9a 55%,#2a2a2a)"></div>
  <div class="pill">Bio Hazardous</div>
</div>

<footer class="abs footer">
  <div class="abs brand" style="left:115px;top:112px;color:var(--white);font-size:44px"><i style="background:var(--red)"></i>BBSA</div>

  <div class="f-title" style="left:385px">Subscribe Us</div>
  <div class="f-text" style="left:385px;top:132px;width:240px;font-size:12px">BBSA offers a 24/7 call-out service to your site</div>
  <div class="f-input">Enter The Email</div>
  <div class="f-sub"><i></i>Subscribe</div>

  <div class="f-title" style="left:696px">Contact Us</div>
  <div class="f-ico" style="top:138px"></div>
  <div class="f-text" style="left:739px;top:134px">BBSA<br>Kiln Lane, Melbourne</div>
  <div class="f-ico" style="top:207px"></div>
  <div class="f-text" style="left:739px;top:212px">+61 3 9000 4417</div>
  <div class="f-ico" style="top:277px"></div>
  <div class="f-text" style="left:739px;top:282px">info@bbsa.com</div>

  <div class="f-title" style="left:928px">Quick Links</div>
  <div class="f-link" style="top:140px">Home</div>
  <div class="f-link" style="top:174px">About</div>
  <div class="f-link" style="top:208px">Why Laser</div>
  <div class="f-link" style="top:242px">Capabilities</div>
  <div class="f-link" style="top:276px">Contact Us</div>

  <div class="f-rule"></div>
  <div class="f-copy">Copyrights@2023.Brightform Beam Services Australia.All Rights Reserved</div>
</footer>

</body>
</html>
```